6-seitiges Prospekt für Messer und Fräser für den industriellen Zuschnitt auf CNC-Flachbettanlagen
Zielgruppe
Hergestellt werden Messer und Fräser für den industriellen Zuschnitt auf CNC-Flachbettanlagen.
Den Einsatz dieser sieht man unter anderem hier: https://www.videoportal-beispiel.de/watch?v=QX7mLpR2aZk
Aufgabenstellung
Der Prospekt wird ein 6-Seiter (gefaltet), Seitengröße DIN A4 Hochformat und wird zweisprachig (englisch/deutsch). Er soll edel und modern anmuten.
Von euch hier soll der Titel und eine Produktseite designt werden.
Die beigestellte Datei enthält alle Beschreibungen/Texte und zu die verwendenen Bilder.

```html
<!DOCTYPE html>
<html lang="de">
<head>
<meta charset="utf-8">
<title>KlingWerk – Messer, Fräser und Zubehör</title>
<link rel="stylesheet" href="https://fonts.googleapis.com/css2?family=Exo+2:ital,wght@0,300;0,400;0,600;0,700;1,300;1,400;1,700&family=Roboto+Condensed:wght@400;700&display=swap">
<style>
:root{
  --red:#c4161c;
  --red-dark:#9c0f14;
  --red-light:#d9262b;
  --ink:#2b2b2b;
  --grey:#6d6d6d;
  --paper:#f7f7f7;
  --panel:#ffffff;
  --stage:#ececec;
  --card:#f1eaea;
  --photo-light:#dfe1e3;
  --photo-mid:#b9bdc1;
}
*{box-sizing:border-box;margin:0;padding:0}
html,body{width:1200px;height:2400px;overflow:hidden}
body{background:var(--stage);font-family:"Roboto Condensed",sans-serif;color:var(--ink);position:relative}

/* ---------- Cover ---------- */
.cover{position:absolute;left:320px;top:60px;width:560px;height:792px;background:var(--paper);box-shadow:0 6px 18px rgba(0,0,0,.15);overflow:hidden}
.cover-red{position:absolute;inset:0 0 145px 0;background:linear-gradient(135deg,var(--red-light),var(--red) 55%,var(--red-dark))}
.cover-url{position:absolute;left:64px;top:54px;color:#fff;font:italic 700 11px "Exo 2",sans-serif}
.cover-title{position:absolute;left:62px;top:128px;color:#fff;font:italic 700 32px/1.2 "Exo 2",sans-serif}
.cover-sub{position:absolute;left:62px;top:222px;color:#fff;font:italic 300 19px "Exo 2",sans-serif}
.cover-photo{position:absolute;left:46px;top:300px;width:514px;height:347px;background:linear-gradient(180deg,rgba(200,204,208,.25),rgba(200,204,208,.55))}
.cover-band{position:absolute;left:0;right:0;bottom:145px;height:6px;background:linear-gradient(#cfcfcf,#e9e9e9)}
.cover .brand{position:absolute;right:44px;bottom:50px;font-size:36px}

/* ---------- Brand ---------- */
.brand{display:flex;align-items:center;gap:8px;font-family:"Exo 2",sans-serif;font-weight:600;color:var(--ink)}
.brand-mark{width:.9em;height:.9em;background:var(--red)}

/* ---------- Leaflet panels ---------- */
.spread{position:absolute;display:flex;box-shadow:0 6px 18px rgba(0,0,0,.14)}
.spread-inner{left:15px;top:900px}
.spread-outer{left:180px;top:1540px}
.panel{position:relative;background:var(--panel);overflow:hidden;border-right:1px solid #e2e2e2}
.spread-inner .panel{width:390px;height:552px}
.spread-outer .panel{width:420px;height:594px}
.panel:last-child{border-right:none}

/* Manufacturing panel */
.mfg{padding:26px 24px 0}
.section-bar{height:14px;background:var(--red);margin:0 -24px;clip-path:polygon(0 0,100% 0,97% 100%,0 100%)}
.section-label{display:inline-block;color:#fff;background:var(--red);font:400 9px "Exo 2",sans-serif;letter-spacing:.5px;padding:2px 8px;margin:-1px 0 8px -24px}
.mfg h3{font:700 10px "Exo 2",sans-serif;margin-bottom:4px}
.mfg p{font-size:8px;line-height:1.35;margin-bottom:4px}
.mfg h4{font:700 9px "Exo 2",sans-serif;margin:6px 0 5px}
.process{display:flex;gap:6px;margin-bottom:12px}
.process figure{flex:1}
.process .shot{height:46px;background:linear-gradient(135deg,#b9c6cc,#6f818b)}
.process .shot.warm{background:linear-gradient(135deg,#c08e74,#5b656c)}
.process .shot.tool{background:linear-gradient(135deg,#8fa3b1,#3e4c57)}
.process figcaption{font-size:6px;line-height:1.25;color:var(--red);text-align:center;margin-top:3px}
.panel-foot{position:absolute;left:24px;right:24px;bottom:14px;display:flex;justify-content:space-between;align-items:flex-end;border-top:1px solid #ddd;padding-top:8px}
.panel-foot .url{font:400 9px "Exo 2",sans-serif;color:var(--grey)}
.panel-foot .brand{font-size:16px}
.spread-outer .mfg p{font-size:8.6px}
.spread-outer .process .shot{height:52px}

/* Product panels */
.products{padding:22px 18px 0}
.range-title{font:600 13px "Exo 2",sans-serif;text-transform:uppercase;line-height:1.05;margin:4px 0 6px}
.range-title span{display:block;font-weight:300;font-style:italic;color:#888;font-size:11px}
.card{position:relative;background:linear-gradient(90deg,#f4f4f4,var(--card));border-top:1px solid #e3c9c9;height:118px;margin-bottom:10px;display:flex;align-items:flex-start;padding:26px 8px 8px}
.card-tag{position:absolute;left:0;top:6px;background:var(--red);color:#fff;font:italic 600 7px "Exo 2",sans-serif;padding:2px 8px 2px 6px;text-transform:uppercase}
.card-tag small{display:block;font-weight:300;font-size:6px}
.card-photo{width:86px;height:78px;flex:none;background:linear-gradient(160deg,var(--photo-light),var(--photo-mid))}
.spec{flex:1;margin-left:10px;font-size:6px;line-height:1.3}
.spec h5{font:700 6.5px "Roboto Condensed",sans-serif;margin-bottom:3px}
.spec-grid{display:grid;grid-template-columns:58px 32px 62px 1fr;column-gap:4px}
.spec-grid dt{font-weight:700}
.spec-grid dd{color:#444}
.contact{position:absolute;left:18px;right:18px;bottom:12px;display:flex;justify-content:space-between;gap:8px;border-top:1px solid #e3c9c9;padding-top:6px;color:var(--red);font-size:7px;line-height:1.3}
.contact b{font-weight:700}
.contact em{font-style:italic;color:#d96b6e}

/* Red outer panel */
.panel.red{background:linear-gradient(150deg,var(--red-light),var(--red) 50%,var(--red-dark));color:#fff;padding:40px 34px}
.quality-bar{display:inline-block;background:rgba(0,0,0,.25);font:400 9px "Exo 2",sans-serif;letter-spacing:.6px;padding:3px 10px 3px 34px;margin:0 0 14px -34px}
.range-list{list-style:none;font:400 15px/1.35 "Exo 2",sans-serif}
.claims{position:absolute;left:34px;right:34px;bottom:40px;display:flex;gap:16px}
.claim{flex:1}
.claim + .claim{border-left:1px solid rgba(255,255,255,.7);padding-left:16px}
.claim h3{font:400 11px/1.2 "Exo 2",sans-serif;text-transform:uppercase;margin-bottom:10px}
.claim .lead{font:400 10.5px/1.3 "Exo 2",sans-serif;margin-bottom:10px}
.claim p{font-size:7.5px;line-height:1.35}
</style>
</head>
<body>

<!-- Cover -->
<section class="cover">
  <div class="cover-red"></div>
  <div class="cover-url">www.klingwerk-beispiel.de</div>
  <h1 class="cover-title">MESSER, FRÄSER UND<br>ZUBEHÖR</h1>
  <div class="cover-sub">BLADES, ROUTER BITS AND ACCESSORIES</div>
  <div class="cover-photo" role="img" aria-label="Produktfoto: vier Schneidmesser und ein Rundmesser aus gebürstetem Stahl"></div>
  <div class="cover-band"></div>
  <div class="brand"><span class="brand-mark"></span>KlingWerk</div>
</section>

<!-- Inner spread -->
<section class="spread spread-inner">
  <article class="panel mfg">
    <div class="section-bar"></div>
    <div class="section-label">HERSTELLUNG</div>
    <h3>Hochwertige Messer und Zubehör</h3>
    <p>Ectaestiisin plit faciumet aut fuga. Natur apedis nimint voloribustis ratur asi nonsed ute explant quatur, ellamet di nias ni de nus, volorruptam autatusam a num natum iur? Agnimentia dolorer uptatur, identiam, sanis mo exeria viderovidios est enditiae consecu llorisi tem dignist ibusciument.</p>
    <p>Ita cusci dolorepres cuptiur am fugitatur simporest vereium volupta tianit litatecum repuda sin rem ipsapellupti dolorum dolupta dit, sam quuntia sed moluptu ribusdam fugit, acerchitios es volumet laut pos re erero inverspicius doloratque nihillab ipientorerum hicimolutа era dior aut eos in paru-mendit voluptam, non</p>
    <h4>Herstellungsprozess</h4>
    <div class="process">
      <figure><div class="shot warm" role="img" aria-label="Foto: Stahlblech beim Laserzuschnitt"></div><figcaption>1. Ectaestiisin plit faciumet aut fuga. Natur apedis nimint voloribustis ratur</figcaption></figure>
      <figure><div class="shot" role="img" aria-label="Foto: ausgestanzte Messerrohlinge"></div><figcaption>2. Ectaestiisin plit faciumet aut fuga. Natur apedis nimint voloribustis ratur</figcaption></figure>
      <figure><div class="shot tool" role="img" aria-label="Foto: Schleifmaschine beim Messerschliff"></div><figcaption>3. Ectaestiisin plit faciumet aut fuga. Natur apedis nimint voloribustis ratur</figcaption></figure>
    </div>
    <div class="section-bar"></div>
    <div class="section-label">HERSTELLUNG</div>
    <h3>Hochwertige Messer und Zubehör</h3>
    <p>Ectaestiisin plit faciumet aut fuga. Natur apedis nimint voloribustis ratur asi nonsed ute explant quatur, ellamet di nias ni de nus, volorruptam autatusam a num natum iur? Agnimentia dolorer uptatur, identiam, sanis mo exeria viderovidios est enditiae consecu llorisi tem dignist ibusciument.</p>
    <h4>Herstellungsprozess</h4>
    <div class="process">
      <figure><div class="shot warm" role="img" aria-label="Foto: Stahlblech beim Laserzuschnitt"></div><figcaption>1. Ectaestiisin plit faciumet aut fuga.</figcaption></figure>
      <figure><div class="shot" role="img" aria-label="Foto: ausgestanzte Messerrohlinge"></div><figcaption>2. Ectaestiisin plit faciumet aut fuga.</figcaption></figure>
      <figure><div class="shot tool" role="img" aria-label="Foto: Schleifmaschine beim Messerschliff"></div><figcaption>3. Ectaestiisin plit faciumet aut fuga.</figcaption></figure>
    </div>
    <div class="panel-foot"><span class="url">www.klingwerk-beispiel.de</span><span class="brand"><span class="brand-mark"></span>KlingWerk</span></div>
  </article>

  <article class="panel products">
    <h2 class="range-title">Flachmesser<span>Flat knife blades</span></h2>
    <div class="card">
      <div class="card-tag">Flachmesser<small>KW143509</small></div>
      <div class="card-photo" role="img" aria-label="Produktfoto: Flachmesser"></div>
      <div class="spec"><h5>Produktinformationen / Product information</h5>
        <dl class="spec-grid">
          <dt>Passend für</dt><dd>Serie G3</dd><dt>Schneidwinkel</dt><dd>30°</dd>
          <dt>Max. Schnitttiefe</dt><dd>6 mm</dd><dt>Schneidart</dt><dd>oszillierend</dd>
          <dt>Schaftbreite</dt><dd>6,2 mm</dd><dt>Spitze / Form</dt><dd>einschneidig</dd>
          <dt>Länge</dt><dd>26,5 mm</dd><dt>Material</dt><dd>Hartmetall</dd>
          <dt>Messerstärke</dt><dd>0,52 mm</dd><dt>Anwendung</dt><dd>Karton, Papier</dd>
        </dl></div>
    </div>
    <div class="card">
      <div class="card-tag">Flachmesser<small>KW143510</small></div>
      <div class="card-photo" role="img" aria-label="Produktfoto: Flachmesser"></div>
      <div class="spec"><h5>Produktinformationen / Product information</h5>
        <dl class="spec-grid">
          <dt>Passend für</dt><dd>Serie G3</dd><dt>Schneidwinkel</dt><dd>25°</dd>
          <dt>Max. Schnitttiefe</dt><dd>6 mm</dd><dt>Schneidart</dt><dd>oszillierend</dd>
          <dt>Schaftbreite</dt><dd>6,2 mm</dd><dt>Spitze / Form</dt><dd>einschneidig</dd>
          <dt>Länge</dt><dd>26,5 mm</dd><dt>Material</dt><dd>Hartmetall</dd>
          <dt>Messerstärke</dt><dd>0,52 mm</dd><dt>Anwendung</dt><dd>Wellpappe, Folie</dd>
        </dl></div>
    </div>
    <h2 class="range-title">Doppelschneidige Messer<span>Double edge blades</span></h2>
    <div class="card">
      <div class="card-tag">Doppelschneidiges Messer<small>KW143520</small></div>
      <div class="card-photo" role="img" aria-label="Produktfoto: doppelschneidiges Messer"></div>
      <div class="spec"><h5>Produktinformationen / Product information</h5>
        <dl class="spec-grid">
          <dt>Passend für</dt><dd>Serie G3</dd><dt>Schneidwinkel</dt><dd>30°</dd>
          <dt>Max. Schnitttiefe</dt><dd>6 mm</dd><dt>Schneidart</dt><dd>ziehend</dd>
          <dt>Schaftbreite</dt><dd>6,2 mm</dd><dt>Spitze / Form</dt><dd>doppelschneidig</dd>
          <dt>Länge</dt><dd>26,5 mm</dd><dt>Material</dt><dd>Hartmetall</dd>
          <dt>Messerstärke</dt><dd>0,52 mm</dd><dt>Anwendung</dt><dd>Leder, Textil</dd>
        </dl></div>
    </div>
    <div class="contact">
      <b>Wunschklinge nicht dabei?<br>Sprechen Sie uns an –<br>wir fertigen individuell.</b>
      <em>Unsere Telefon Hotline ist<br>Montag bis Freitag von<br>8.00–16.30 Uhr für Sie da.</em>
      <b>Telefon: +49 (0)123 / 45 678 900</b>
    </div>
  </article>

  <article class="panel products">
    <div class="card">
      <div class="card-tag">Doppelschneidiges Messer<small>KW143521</small></div>
      <div class="card-photo" role="img" aria-label="Produktfoto: doppelschneidiges Messer"></div>
      <div class="spec"><h5>Produktinformationen / Product information</h5>
        <dl class="spec-grid">
          <dt>Passend für</dt><dd>Serie G3</dd><dt>Schneidwinkel</dt><dd>30°</dd>
          <dt>Max. Schnitttiefe</dt><dd>6 mm</dd><dt>Schneidart</dt><dd>ziehend</dd>
          <dt>Schaftbreite</dt><dd>6,2 mm</dd><dt>Spitze / Form</dt><dd>doppelschneidig</dd>
          <dt>Länge</dt><dd>26,5 mm</dd><dt>Material</dt><dd>Hartmetall</dd>
          <dt>Messerstärke</dt><dd>0,52 mm</dd><dt>Anwendung</dt><dd>Karton, Papier</dd>
        </dl></div>
    </div>
    <h2 class="range-title">Doppelschneidige Messer<span>Double edge blades</span></h2>
    <div class="card">
      <div class="card-tag">Flachmesser<small>KW143522</small></div>
      <div class="card-photo" role="img" aria-label="Produktfoto: breites Flachmesser"></div>
      <div class="spec"><h5>Produktinformationen / Product information</h5>
        <dl class="spec-grid">
          <dt>Passend für</dt><dd>Serie G3</dd><dt>Schneidwinkel</dt><dd>35°</dd>
          <dt>Max. Schnitttiefe</dt><dd>6 mm</dd><dt>Schneidart</dt><dd>oszillierend</dd>
          <dt>Schaftbreite</dt><dd>6,2 mm</dd><dt>Spitze / Form</dt><dd>trapezförmig</dd>
          <dt>Länge</dt><dd>26,5 mm</dd><dt>Material</dt><dd>Hartmetall</dd>
          <dt>Messerstärke</dt><dd>0,52 mm</dd><dt>Anwendung</dt><dd>Schaumstoff</dd>
        </dl></div>
    </div>
    <div class="card">
      <div class="card-tag">Flachmesser<small>KW143523</small></div>
      <div class="card-photo" role="img" aria-label="Produktfoto: Rundmesser-Segment"></div>
      <div class="spec"><h5>Produktinformationen / Product information</h5>
        <dl class="spec-grid">
          <dt>Passend für</dt><dd>Serie G3</dd><dt>Schneidwinkel</dt><dd>30°</dd>
          <dt>Max. Schnitttiefe</dt><dd>6 mm</dd><dt>Schneidart</dt><dd>rotierend</dd>
          <dt>Schaftbreite</dt><dd>6,2 mm</dd><dt>Spitze / Form</dt><dd>rund</dd>
          <dt>Länge</dt><dd>26,5 mm</dd><dt>Material</dt><dd>Hartmetall</dd>
          <dt>Messerstärke</dt><dd>0,52 mm</dd><dt>Anwendung</dt><dd>Textil, Folie</dd>
        </dl></div>
    </div>
    <div class="contact">
      <b>Looking for other items?<br>Do not hesitate to contact us –<br>we create knives individually!</b>
      <em>Our service hotline is available<br>monday to friday from<br>8.00 a.m. to 4.30 p.m.</em>
      <b>Phone: +49 (0)123 / 45 678 900</b>
    </div>
  </article>
</section>

<!-- Outer spread -->
<section class="spread spread-outer">
  <article class="panel mfg">
    <div class="section-bar"></div>
    <div class="section-label">HERSTELLUNG</div>
    <h3>Hochwertige Messer und Zubehör</h3>
    <p>Ectaestiisin plit faciumet aut fuga. Natur apedis nimint voloribustis ratur asi nonsed ute explant quatur, ellamet di nias ni de nus, volorruptam autatusam a num natum iur? Agnimentia dolorer uptatur, identiam, sanis mo exeria viderovidios est enditiae consecu llorisi tem dignist ibusciument.</p>
    <p>Ita cusci dolorepres cuptiur am fugitatur simporest vereium volupta tianit litatecum repuda sin rem ipsapellupti dolorum dolupta dit, sam quuntia sed moluptu ribusdam fugit, acerchitios es volumet laut pos re erero inverspicius doloratque nihillab ipientorerum hicimolutа era dior aut eos in paru-mendit voluptam, non</p>
    <h4>Herstellungsprozess</h4>
    <div class="process">
      <figure><div class="shot warm" role="img" aria-label="Foto: Stahlblech beim Laserzuschnitt"></div><figcaption>1. Ectaestiisin plit faciumet aut fuga. Natur apedis nimint voloribustis ratur</figcaption></figure>
      <figure><div class="shot" role="img" aria-label="Foto: ausgestanzte Messerrohlinge"></div><figcaption>2. Ectaestiisin plit faciumet aut fuga. Natur apedis nimint voloribustis ratur</figcaption></figure>
      <figure><div class="shot tool" role="img" aria-label="Foto: Schleifmaschine beim Messerschliff"></div><figcaption>3. Ectaestiisin plit faciumet aut fuga. Natur apedis nimint voloribustis ratur</figcaption></figure>
    </div>
    <div class="section-bar"></div>
    <div class="section-label">HERSTELLUNG</div>
    <h3>Hochwertige Messer und Zubehör</h3>
    <p>Ectaestiisin plit faciumet aut fuga. Natur apedis nimint voloribustis ratur asi nonsed ute explant quatur, ellamet di nias ni de nus, volorruptam autatusam a num natum iur? Agnimentia dolorer uptatur, identiam, sanis mo exeria viderovidios est enditiae consecu llorisi tem dignist ibusciument.</p>
    <h4>Herstellungsprozess</h4>
    <div class="process">
      <figure><div class="shot warm" role="img" aria-label="Foto: Stahlblech beim Laserzuschnitt"></div><figcaption>1. Ectaestiisin plit faciumet aut fuga.</figcaption></figure>
      <figure><div class="shot" role="img" aria-label="Foto: ausgestanzte Messerrohlinge"></div><figcaption>2. Ectaestiisin plit faciumet aut fuga.</figcaption></figure>
      <figure><div class="shot tool" role="img" aria-label="Foto: Schleifmaschine beim Messerschliff"></div><figcaption>3. Ectaestiisin plit faciumet aut fuga.</figcaption></figure>
    </div>
    <div class="panel-foot"><span class="url">www.klingwerk-beispiel.de</span><span class="brand"><span class="brand-mark"></span>KlingWerk</span></div>
  </article>

  <article class="panel red">
    <div class="quality-bar">PREMIUM QUALITÄT MADE IN GERMANY</div>
    <ul class="range-list">
      <li>Cuttermesser</li>
      <li>Plottermesser</li>
      <li>Oszilliermesser</li>
      <li>Ziehmesser</li>
      <li>Rotationsmesser</li>
      <li>Passepartoutmesser</li>
      <li>Kisscut-Messer</li>
      <li>Fräser</li>
    </ul>
    <div class="claims">
      <div class="claim">
        <h3>Vom ersten Schnitt<br>besser abschneiden.</h3>
        <p class="lead">Die Schnittergebnisse Ihres Cutters sind immer nur so gut, wie die eingesetzten Messer und Fräser.</p>
        <p>Aus diesem Grunde hat sich die KlingWerk GmbH das Ziel gesetzt, nur qualitativ hochwertiges Zubehör zu liefern. Alle unsere Messer und Fräser werden ausschließlich in Deutschland gefertigt!</p>
      </div>
      <div class="claim">
        <h3>For better results<br>from the first cut.</h3>
        <p class="lead">The cutting results of your cutter are only as good as the knives and cutters used.</p>
        <p>For this reason, KlingWerk GmbH has set itself the goal of supplying only high-quality accessories. All our knives and cutters are made exclusively in Germany!</p>
      </div>
    </div>
  </article>
</section>

</body>
</html>
```